Looking for a cool, modern Cannabis Jar Label

I want you to come up with a better, modern look for a label.

I need it sized to 4” x 3” - I plan to print directly to label printer.

I want you to use Photoshop and deliver me a layered PSD file that I can edit and modify the information as needed..

The label information will need to include places for:
(1) Strain Name - most important part of label - larger font size than rest - example Kestrel Mist, PLV #7, Juniper Hollow
(2) Pricing - for Gram, 1/8, 1/4, 1/2. and Ounce
(3) Strain Designation (Hybrid, Indica or Sativa) - maybe color coded, different color for Indica v. Sativa, just an idea
(4) THC and CBD percentages - for example 23% THC and 0.05% CBD
(5) Farm name - a place where we can add the name/logo of the business that produced the product. example - Ovenrow Farms

I have attached a simple mockup showing the information.

I have also attached a few samples of labels we like to give you an idea of the look and feel we are going for.

I am wanting a very clean, modern, classy, readable look.The font will use is Gotham Font.

HI Everyone! Thank you for all of your designs. I am requesting an extension because I need more time to give adequate feedback to the designers. Thank you for your participation and all of your efforts! I will be making a decision soon!

• Gotham Font

• Thank you for your designs. I am sorry i have been slow in providing feedback, things have been really busy around here!
• I wanted to give some group general feedback. After reviewing all of the designs, there is a common theme among all of the designs that I would like to see changed.
• I would like to see the per gram pricing more prominent on the label. This is what most people are looking for when they are purchasing the product. So I would like to see this stand out from the other pricing tiers. As I think about it, they don't all need to be grouped together in a line. You could have the Per Gram pricing front and center some where and then the other pricing tiers grouped together somewhere else on the label.
• This is the order of importance of items on the label. Items at the the top of the list should be bigger than those below it.
• 1. Strain name
• 2. Pricing - being per gram the most important of all prices
• 3. THC/CBD percentages
• 4. Strain Type (indica, sativa, hybrid)
• 5. Farm name/logo
• When laying out these labels, they will be going on rounded jars and they will be on display. Think of jars with fancy labels in a candy store. They need to be eye catchy, appealing, but easy read.
• Thank you for all of your hard work, everyone is doing a great job.
• Best,
• Neta

```html
<!DOCTYPE html>
<html lang="en">
<head>
<meta charset="utf-8">
<title>Kestrel Mist – Jar Label</title>
<link href="https://fonts.googleapis.com/css2?family=Montserrat:wght@300;400;700&display=swap" rel="stylesheet">
<style>
  :root {
    --ink: #000000;
    --paper: #ffffff;
    --maroon: #870505;
    --rose: #a84b4b;
    --blush: #eed7d7;
    --blush-deep: #e2c4c4;
    --blush-mid: #d9b0b0;
    --blush-tri: #e3c0c0;
  }
  * { box-sizing: border-box; margin: 0; padding: 0; }
  html, body {
    width: 1200px; height: 917px; overflow: hidden;
    background: var(--paper);
    font-family: "Montserrat", sans-serif;
  }
  .label {
    position: absolute; left: 33px; top: 33px;
    width: 1125px; height: 844px;
    background: var(--ink);
  }
  .label > * { position: absolute; }

  /* Strain name header */
  .strain {
    left: 5px; top: 5px; width: 1047px; height: 251px;
    background: var(--maroon); color: var(--paper);
  }
  .strain-name {
    position: absolute; left: 37px; white-space: nowrap;
    font-weight: 400; line-height: 1; letter-spacing: -1px;
    text-shadow: 1px 2px 3px rgba(0,0,0,.35);
  }
  .strain-name.primary { top: 20px; font-size: 122px; }
  .strain-name.secondary { top: 148px; font-size: 100px; }

  .strain-type {
    left: 1052px; top: 5px; width: 68px; height: 251px;
    display: flex; flex-direction: column; align-items: center; justify-content: center;
    color: var(--paper); font-size: 31px; font-weight: 400; line-height: 36px;
  }

  /* Pricing row */
  .pricing {
    left: 5px; top: 256px; width: 1115px; height: 334px;
    display: flex; background: var(--paper);
  }
  .tier {
    flex: 1; display: flex; flex-direction: column; align-items: center;
  }
  .tier:nth-child(2), .tier:nth-child(4) { background: var(--blush); }
  .tier:nth-child(3) { background: var(--blush-deep); }
  .tier-price {
    margin-top: 68px; font-size: 74px; font-weight: 300; color: var(--ink); line-height: 1;
    letter-spacing: -1px;
  }
  .tier-unit {
    margin-top: 52px; font-size: 96px; font-weight: 300; color: var(--maroon); line-height: 1;
  }

  .rule { left: 5px; top: 590px; width: 1115px; height: 7px; background: var(--maroon); }

  /* Potency */
  .potency { left: 5px; top: 597px; width: 766px; height: 242px; }
  .potency svg { position: absolute; inset: 0; }
  .potency-label, .potency-value { position: absolute; width: 300px; text-align: center; line-height: 1; }
  .potency-label {
    top: 42px; font-size: 47px; font-weight: 700; color: var(--paper);
    text-shadow: 2px 3px 3px rgba(0,0,0,.45);
  }
  .potency-value { top: 150px; font-size: 84px; font-weight: 400; color: var(--ink); letter-spacing: -1px; }
  .potency-value sup { font-size: 36px; vertical-align: top; position: relative; top: 4px; margin-left: 2px; }
  .thc { left: 4px; }
  .cbd { left: 431px; }

  /* Grower */
  .grower { left: 771px; top: 597px; width: 349px; height: 242px; background: var(--paper); }
  .grower-title {
    height: 59px; background: var(--maroon); color: var(--paper);
    font-size: 37px; font-weight: 400; text-align: center; line-height: 62px;
  }
  .grower-name {
    height: 183px; display: flex; align-items: center; justify-content: center; gap: 14px;
    font-size: 34px; font-weight: 700; color: var(--ink);
  }
  .grower-mark { width: 30px; height: 30px; border-radius: 50%; background: var(--ink); }
</style>
</head>
<body>
  <div class="label">
    <header class="strain">
      <div class="strain-name primary">Kestrel Mist</div>
      <div class="strain-name secondary">Juniper Hollow</div>
    </header>
    <div class="strain-type" aria-label="Hybrid">
      <span>H</span><span>Y</span><span>B</span><span>R</span><span>I</span><span>D</span>
    </div>

    <section class="pricing">
      <div class="tier"><span class="tier-price">$10</span><span class="tier-unit">g.</span></div>
      <div class="tier"><span class="tier-price">$35</span><span class="tier-unit">1/8</span></div>
      <div class="tier"><span class="tier-price">$70</span><span class="tier-unit">1/4</span></div>
      <div class="tier"><span class="tier-price">$140</span><span class="tier-unit">1/2</span></div>
      <div class="tier"><span class="tier-price">$280</span><span class="tier-unit">oz</span></div>
    </section>

    <div class="rule"></div>

    <section class="potency">
      <svg width="766" height="242" viewBox="0 0 766 242" aria-hidden="true">
        <rect x="0" y="0" width="766" height="120" fill="var(--rose)"/>
        <rect x="0" y="120" width="766" height="122" fill="var(--blush-mid)"/>
        <polygon points="300,0 431,0 365,120" fill="var(--blush-tri)"/>
        <polygon points="298,242 436,242 365,120" fill="var(--rose)"/>
      </svg>
      <div class="potency-label thc">THC</div>
      <div class="potency-label cbd">CBD</div>
      <div class="potency-value thc">28<sup>%</sup></div>
      <div class="potency-value cbd">0.05<sup>%</sup></div>
    </section>

    <section class="grower">
      <div class="grower-title">Grown by</div>
      <div class="grower-name"><span class="grower-mark"></span>Ovenrow Farms</div>
    </section>
  </div>
</body>
</html>
```